Brightmill Data Works

Our company is about IT hardwares and IT solutions. IT hardware such as PC, RAMS, storage and servers. IT solutions such as project management, BA. We are also selling new technology too.

Target Market(s)

Consumer, Small to Medium Business, Corporate

Requirements
Must have
• The business card must have the following:
• Name:
• Title:
• Contact Number:
• Email address:
• Website:
• Color: Must match the logo color upgrade

```html
<!DOCTYPE html>
<html lang="en">
<head>
<meta charset="utf-8">
<title>Brightmill Data Works – Business Card</title>
<link rel="stylesheet" href="https://fonts.googleapis.com/css2?family=Open+Sans:wght@400;600;700&display=swap">
<style>
  :root {
    --stage: #262626;
    --card: #0f0f10;
    --card-edge: #1c1c1e;
    --accent: #e8952a;
    --ink: #ffffff;
    --ink-soft: #d9d9d9;
    --rule: #bdbdbd;
  }
  * { box-sizing: border-box; margin: 0; padding: 0; }
  html, body { width: 1200px; height: 900px; overflow: hidden; }
  body {
    background: var(--stage);
    font-family: "Open Sans", Arial, sans-serif;
    display: flex; flex-direction: column; align-items: center; justify-content: center;
    gap: 40px;
  }
  .card {
    position: relative;
    width: 700px; height: 400px;
    background: linear-gradient(160deg, var(--card-edge), var(--card) 55%);
    border-radius: 22px;
    box-shadow: 0 14px 30px rgba(0,0,0,.45);
    color: var(--ink);
  }
  .brand-mark {
    display: flex; align-items: center; gap: 14px;
    font-weight: 700; text-transform: uppercase; letter-spacing: 1px;
    color: var(--ink);
  }
  .brand-dot { width: 18px; height: 18px; border-radius: 50%; background: var(--accent); flex: none; }

  /* back */
  .card-back { display: flex; flex-direction: column; align-items: center; justify-content: center; gap: 34px; }
  .card-back .brand-mark { font-size: 40px; }
  .tagline { font-size: 16px; font-weight: 600; letter-spacing: .5px; color: var(--ink-soft); text-transform: uppercase; }

  /* front */
  .card-front .brand-mark { position: absolute; right: 48px; top: 120px; font-size: 30px; }
  .divider { position: absolute; left: 44px; right: 44px; top: 200px; height: 1px; background: var(--rule); }
  .person { position: absolute; left: 48px; top: 160px; }
  .person-name { font-size: 24px; font-weight: 600; color: var(--accent); text-transform: uppercase; line-height: 34px; }
  .person-title { margin-top: 10px; font-size: 19px; color: var(--ink-soft); }
  .contacts { position: absolute; right: 48px; top: 222px; list-style: none; text-align: right; }
  .contacts li { display: flex; align-items: center; justify-content: flex-end; gap: 12px; font-size: 18px; line-height: 32px; color: var(--ink-soft); }
  .contacts svg { width: 16px; height: 16px; fill: var(--accent); flex: none; }
</style>
</head>
<body>
  <section class="card card-back">
    <div class="brand-mark"><span class="brand-dot"></span>Brightmill Data Works</div>
    <p class="tagline">IT Hardwares and IT Solutions</p>
  </section>

  <section class="card card-front">
    <div class="brand-mark"><span class="brand-dot"></span>Brightmill Data Works</div>
    <div class="divider"></div>
    <div class="person">
      <p class="person-name">Marcus Hale</p>
      <p class="person-title">Managing Director</p>
    </div>
    <ul class="contacts">
      <li>044-208 317 562
        <svg viewBox="0 0 16 16" aria-hidden="true"><path d="M3 1h3l1.5 4-2 1.3a9 9 0 0 0 4.2 4.2L11 8.5l4 1.5v3a2 2 0 0 1-2 2A12 12 0 0 1 1 3a2 2 0 0 1 2-2z"/></svg>
      </li>
      <li>info@brightmill.com
        <svg viewBox="0 0 16 16" aria-hidden="true"><path d="M1 3h14v10H1zM2 4.2v.4l6 4.2 6-4.2v-.4z" fill-rule="evenodd"/></svg>
      </li>
      <li>www.brightmilldata.com
        <svg viewBox="0 0 16 16" aria-hidden="true"><circle cx="8" cy="8" r="7"/><path d="M1 8h14M8 1c-3 3.5-3 10.5 0 14M8 1c3 3.5 3 10.5 0 14" stroke="#0f0f10" stroke-width="1.2" fill="none"/></svg>
      </li>
    </ul>
  </section>
</body>
</html>
```